Tallowood building company Business card design

I need a business card design for my company. I have a logo but dont have business cards with our logo..

www.tallowoodbuildingco.com.au

The logo is on the website

I need the same details as this design I have attached. we have changed the logo and colours. just like the website

Building

```html
<!DOCTYPE html>
<html lang="en">
<head>
<meta charset="utf-8">
<title>Tallowood Building – Business Card</title>
<link rel="stylesheet" href="https://fonts.googleapis.com/css2?family=Cinzel:wght@500;600&family=Lato:wght@400;700&display=swap">
<style>
  :root {
    --backdrop: #b9b9b9;
    --card: #fbfbfa;
    --brand-blue: #1a8ccc;
    --arc-grey: #c4c6c8;
    --ink: #1c1c1c;
    --white: #ffffff;
  }
  * { margin: 0; padding: 0; box-sizing: border-box; }
  html, body {
    width: 1200px; height: 800px; overflow: hidden;
    background: var(--backdrop);
  }
  .card {
    position: absolute; left: 100px; top: 114px;
    width: 1000px; height: 572px;
    background: var(--card);
    overflow: hidden;
  }
  .card__band { position: absolute; inset: 0; width: 100%; height: 100%; }
  .band__arc { fill: var(--arc-grey); }
  .band__fill { fill: var(--brand-blue); }

  .brand {
    position: absolute; left: 150px; top: 110px;
    display: flex; align-items: center; gap: 14px;
    font-family: "Cinzel", serif; font-weight: 600;
    font-size: 38px; line-height: 1.05; color: var(--brand-blue);
    letter-spacing: 1px;
  }
  .brand__mark { width: 22px; height: 22px; background: var(--brand-blue); flex: none; }

  .person {
    position: absolute; right: 90px; top: 236px; text-align: right;
  }
  .person__name {
    font-family: "Cinzel", serif; font-weight: 600; font-size: 32px;
    color: var(--ink); letter-spacing: 1px;
  }
  .person__role {
    font-family: "Lato", sans-serif; font-size: 23px; color: var(--brand-blue);
    letter-spacing: 1px; margin-top: 2px;
  }

  .services {
    position: absolute; left: 50px; top: 312px;
    font-family: "Lato", sans-serif; font-size: 19px; line-height: 1.25;
    color: var(--white);
  }
  .divider {
    position: absolute; left: 398px; top: 395px; width: 2px; height: 120px;
    background: var(--white);
  }
  .contacts {
    position: absolute; left: 420px; top: 398px; list-style: none;
    font-family: "Lato", sans-serif; font-size: 22px; color: var(--white);
  }
  .contacts__item { display: flex; align-items: center; gap: 14px; height: 38px; white-space: nowrap; }
  .contacts__icon { width: 24px; height: 24px; flex: none; }
</style>
</head>
<body>
  <div class="card">
    <svg class="card__band" viewBox="0 0 1000 572" preserveAspectRatio="none" aria-hidden="true">
      <path class="band__arc" d="M0,272 Q520,128 1000,572 L0,572 Z"/>
      <path class="band__fill" d="M0,290 Q500,150 960,572 L0,572 Z"/>
    </svg>

    <div class="brand">
      <span class="brand__mark"></span>
      <span class="brand__name">Tallowood<br>Building</span>
    </div>

    <div class="person">
      <div class="person__name">Radu Petrescu</div>
      <div class="person__role">Director</div>
    </div>

    <p class="services">New Homes, Addition &amp; Renovation<br>Domestic &amp; Commercial Builders</p>

    <div class="divider"></div>

    <ul class="contacts">
      <li class="contacts__item">
        <svg class="contacts__icon" viewBox="0 0 24 24" fill="none" stroke="#fff" stroke-width="1.8"><path d="M3 8c0-2 4-4 9-4s9 2 9 4l-3 2-2-2H8L6 10z" fill="#fff"/><rect x="6" y="12" width="12" height="8" rx="1"/></svg>
        <span>9412 5530</span>
      </li>
      <li class="contacts__item">
        <svg class="contacts__icon" viewBox="0 0 24 24" fill="none" stroke="#fff" stroke-width="1.8"><rect x="6" y="2" width="12" height="20" rx="2"/><line x1="10" y1="18.5" x2="14" y2="18.5"/></svg>
        <span>0423918264 (Radu)</span>
      </li>
      <li class="contacts__item">
        <svg class="contacts__icon" viewBox="0 0 24 24" fill="none" stroke="#fff" stroke-width="1.8"><rect x="2" y="5" width="20" height="14" rx="1"/><path d="M2 5l10 8 10-8"/></svg>
        <span>info@tallowoodbuildingco.com.au</span>
      </li>
    </ul>
  </div>
</body>
</html>
```